Need Business Card ASAP

We need a business card design for a meeting coming up in a few days. The company name is Harlow Ridge Building and Construction and the logo is attached. Something clean, cool, and contemporary that we can get to a printer right away. Attached is the business card for Volmar Energy, an affiliated company, which we like. Instead of the hawk on the back, you could use the attached "D". We'll also be needing matching letterhead in the near future, so ideas for that are welcome.

```html
<!DOCTYPE html>
<html lang="en">
<head>
<meta charset="utf-8">
<title>Harlow Ridge Building and Construction – Business Card</title>
<link href="https://fonts.googleapis.com/css2?family=Exo+2:wght@400;500;600&display=swap" rel="stylesheet">
<style>
  :root {
    --stage: #3a3a3a;
    --paper: #ffffff;
    --khaki: #b9ae80;
    --khaki-light: #d2c9a1;
    --ink: #1d1b1b;
    --text-dark: #1d1b1b;
    --text-light: #ffffff;
  }
  * { margin: 0; padding: 0; box-sizing: border-box; }
  html, body {
    width: 1200px; height: 819px; overflow: hidden;
    background: var(--stage);
    font-family: "Exo 2", sans-serif;
  }
  .card {
    position: absolute; left: 100px; top: 124px;
    width: 1000px; height: 572px;
    background: var(--paper);
    overflow: hidden;
    box-shadow: 0 18px 40px rgba(0,0,0,.45);
  }
  .card-shapes { position: absolute; inset: 0; }
  .holder { position: absolute; left: 70px; top: 228px; color: var(--text-light); }
  .holder-name { font-size: 40px; font-weight: 500; letter-spacing: 3px; line-height: 1; }
  .holder-rule { width: 250px; height: 8px; background: var(--khaki); margin: 12px 0 10px; }
  .holder-title { font-size: 19px; font-weight: 400; letter-spacing: 2px; }
  .brand {
    position: absolute; left: 600px; top: 70px;
    width: 210px; height: 150px;
    background: var(--khaki-light);
    display: flex; flex-direction: column; justify-content: center; align-items: center; gap: 10px;
    padding: 14px;
  }
  .brand-mark { width: 26px; height: 26px; background: var(--ink); }
  .brand-name {
    font-size: 17px; font-weight: 600; color: var(--ink);
    text-align: center; line-height: 1.2;
  }
  .contact {
    position: absolute; display: flex; align-items: center; gap: 10px;
    font-size: 20px; font-weight: 400; color: var(--text-dark); letter-spacing: .5px;
    white-space: nowrap; line-height: 1.25;
  }
  .contact svg { width: 20px; height: 20px; flex: none; fill: var(--ink); }
  .contact-web { left: 600px; top: 262px; }
  .contact-phone { left: 600px; top: 334px; }
  .contact-mobile { left: 790px; top: 334px; }
  .contact-email { left: 330px; top: 466px; }
  .contact-address { left: 640px; top: 428px; align-items: flex-start; }
</style>
</head>
<body>
  <main class="card">
    <svg class="card-shapes" viewBox="0 0 1000 572" aria-hidden="true">
      <!-- left khaki panel, upper -->
      <rect x="0" y="0" width="300" height="190" fill="var(--khaki)"/>
      <!-- left khaki panel, lower with slanted edge -->
      <polygon points="0,350 380,350 250,572 0,572" fill="var(--khaki)"/>
      <!-- black name band with stepped shoulder -->
      <polygon points="0,190 430,190 430,120 470,120 470,40 1000,40 1000,60 490,60 490,140 520,140 520,350 0,350" fill="var(--ink)"/>
      <!-- right edge stripe -->
      <rect x="958" y="60" width="42" height="512" fill="var(--ink)"/>
      <!-- khaki contact band -->
      <rect x="560" y="240" width="398" height="140" fill="var(--khaki-light)"/>
      <rect x="560" y="306" width="398" height="4" fill="var(--paper)"/>
      <!-- address block -->
      <polygon points="600,400 958,400 958,572 520,572" fill="var(--khaki-light)"/>
      <!-- white divider line -->
      <line x1="0" y1="540" x2="262" y2="540" stroke="var(--paper)" stroke-width="4"/>
    </svg>

    <section class="holder">
      <h1 class="holder-name">EVAN MARSH</h1>
      <div class="holder-rule"></div>
      <p class="holder-title">GENERAL MANAGER</p>
    </section>

    <div class="brand">
      <span class="brand-mark"></span>
      <span class="brand-name">Harlow Ridge Building and Construction</span>
    </div>

    <p class="contact contact-web">
      <svg viewBox="0 0 20 20"><circle cx="10" cy="10" r="9" fill="none" stroke="#1d1b1b" stroke-width="1.6"/><ellipse cx="10" cy="10" rx="4" ry="9" fill="none" stroke="#1d1b1b" stroke-width="1.4"/><line x1="1" y1="10" x2="19" y2="10" stroke="#1d1b1b" stroke-width="1.4"/></svg>
      www.harlowridgebuild.com
    </p>
    <p class="contact contact-phone">
      <svg viewBox="0 0 20 20"><path d="M4 2l4 1 1 4-2 2a11 11 0 0 0 4 4l2-2 4 1 1 4-2 2C9 18 2 11 2 4z"/></svg>
      021 555 0142
    </p>
    <p class="contact contact-mobile">
      <svg viewBox="0 0 20 20"><rect x="5" y="1" width="10" height="18" rx="2" fill="none" stroke="#1d1b1b" stroke-width="1.8"/><circle cx="10" cy="16" r="1.2"/></svg>
      021 555 0187
    </p>
    <p class="contact contact-email">
      <svg viewBox="0 0 20 20"><rect x="1" y="4" width="18" height="12"/><polyline points="1,4 10,11 19,4" fill="none" stroke="#fff" stroke-width="1.5"/></svg>
      evan@hrbc-build.com
    </p>
    <p class="contact contact-address">
      <svg viewBox="0 0 20 20"><path d="M10 1a6 6 0 0 1 6 6c0 5-6 12-6 12S4 12 4 7a6 6 0 0 1 6-6z"/><circle cx="10" cy="7" r="2.2" fill="#d2c9a1"/></svg>
      <span>42 Quarry Lane, Unit 3,<br>Fenwick Park</span>
    </p>
  </main>
</body>
</html>
```